20 year old business card needs re-design

We need to redesign our corporate business card look. We need something that appears more modern, eye catchy but professional.

Target Market(s)

manufacturing industry

Industry/Entity Type

Manufacturer

Contact Information for Business Card

One side can have the logo. Other side can have contact information.

Font styles to use
Serif

Colors
3277b5
33b8a4
ffffff

Requirements
Must have
• Eye catchy - need to standout from the crowd. company logo cannot change. Full name, job title, phone number and email address.
Should not have
• Fax, business address is not necessary.

```html
<!DOCTYPE html>
<html lang="en">
<head>
<meta charset="utf-8">
<title>Corvane Industrial — Business Card</title>
<link rel="stylesheet" href="https://fonts.googleapis.com/css2?family=Oswald:wght@500&family=Work+Sans:wght@400;600&display=swap">
<style>
  :root {
    --stage: #161616;
    --card: #262626;
    --card-edge: #2e2e2e;
    --teal: #33b8a4;
    --blue: #3277b5;
    --white: #ffffff;
    --soft: #d9d9d9;
    --logo: #c9c9c9;
  }
  * { box-sizing: border-box; margin: 0; padding: 0; }
  html, body {
    width: 1200px; height: 900px; overflow: hidden;
    background: var(--stage);
  }
  .sheet {
    width: 1200px; height: 900px;
    display: flex; flex-direction: column; align-items: center; justify-content: center;
    gap: 40px;
  }
  .card {
    position: relative;
    width: 640px; height: 366px;
    background: linear-gradient(160deg, var(--card) 0%, var(--card-edge) 100%);
    box-shadow: 0 14px 30px rgba(0,0,0,.55);
    overflow: hidden;
  }
  .card__band {
    position: absolute; left: 0; right: 0; bottom: 0;
    height: 9px; background: var(--teal);
  }

  /* Front */
  .front__brand {
    position: absolute; left: 0; right: 0; top: 118px;
    text-align: center;
    font-family: "Work Sans", sans-serif; font-weight: 600;
    color: var(--logo);
    font-size: 44px; letter-spacing: 1px; line-height: 1;
  }
  .front__brand-sub {
    display: block; margin-top: 12px;
    font-size: 13px; letter-spacing: 14px;
  }
  .front__web {
    position: absolute; left: 0; right: 0; bottom: 44px;
    text-align: center;
    font-family: "Work Sans", sans-serif; font-weight: 400;
    color: var(--white); font-size: 13px; letter-spacing: 2px;
  }

  /* Back */
  .back__layout {
    position: absolute; left: 0; right: 0; top: 150px;
    display: flex; align-items: center; justify-content: center; gap: 28px;
  }
  .back__identity { text-align: right; }
  .back__name {
    font-family: "Oswald", sans-serif; font-weight: 500;
    color: var(--teal); font-size: 34px; letter-spacing: 1.5px; line-height: 1.05;
    text-transform: uppercase;
  }
  .back__title {
    font-family: "Work Sans", sans-serif; font-weight: 400;
    color: var(--white); font-size: 15px; margin-top: 2px;
  }
  .back__divider {
    width: 1.5px; height: 66px;
    background: linear-gradient(to bottom, transparent, var(--blue), transparent);
  }
  .back__contacts { list-style: none; }
  .back__contact {
    display: flex; align-items: center; gap: 12px;
    font-family: "Work Sans", sans-serif; font-weight: 400;
    color: var(--soft); font-size: 15px; letter-spacing: .6px; line-height: 24px;
  }
  .back__icon { width: 14px; height: 14px; flex: none; }
</style>
</head>
<body>
<main class="sheet">
  <section class="card card--front" aria-label="Card front">
    <div class="front__brand">Corvane<span class="front__brand-sub">INDUSTRIAL</span></div>
    <div class="front__web">corvaneindustrial.com</div>
    <div class="card__band"></div>
  </section>

  <section class="card card--back" aria-label="Card back">
    <div class="back__layout">
      <div class="back__identity">
        <div class="back__name">Dana Whitlow</div>
        <div class="back__title">Senior Project Manager</div>
      </div>
      <div class="back__divider"></div>
      <ul class="back__contacts">
        <li class="back__contact">
          <svg class="back__icon" viewBox="0 0 14 14" aria-hidden="true"><rect x="4" y="1" width="6" height="12" rx="1" fill="none" stroke="#33b8a4" stroke-width="1.3"/><line x1="6" y1="11" x2="8" y2="11" stroke="#33b8a4" stroke-width="1"/></svg>
          555-014-2200 xt 201
        </li>
        <li class="back__contact">
          <svg class="back__icon" viewBox="0 0 14 14" aria-hidden="true"><rect x="1" y="3" width="12" height="8" fill="#33b8a4"/><path d="M1 3 L7 8 L13 3" fill="none" stroke="#262626" stroke-width="1.2"/></svg>
          dana@corvaneindustrial.com
        </li>
        <li class="back__contact">
          <svg class="back__icon" viewBox="0 0 14 14" aria-hidden="true"><circle cx="6" cy="6" r="4" fill="none" stroke="#33b8a4" stroke-width="1.8"/><line x1="9" y1="9" x2="13" y2="13" stroke="#33b8a4" stroke-width="2"/></svg>
          CorvaneIndustrial.com
        </li>
      </ul>
    </div>
    <div class="card__band"></div>
  </section>
</main>
</body>
</html>
```